MV Decor

There is a sample provided with the arabic text of the business card. please copy paste the same text and the same Logo (The two triangles) Just try to incorproate the Brown background attached (you are free to change the colors) Id like the colors to be mainly shades of black and red.

```html
<!DOCTYPE html>
<html lang="ar">
<head>
<meta charset="utf-8">
<title>MV Decor – Business Card</title>
<link rel="stylesheet" href="https://fonts.googleapis.com/css2?family=Tajawal:wght@400;500&family=Aref+Ruqaa:wght@400&family=Roboto:wght@400&display=swap">
<style>
  :root {
    --backdrop: #5b3b24;
    --card-red: #d01f45;
    --card-red-light: #e13759;
    --card-red-deep: #c91b40;
    --band-dark: #262523;
    --ink-light: #ffffff;
    --bullet: #1e1d1c;
  }
  * { margin: 0; padding: 0; box-sizing: border-box; }
  html, body { width: 1125px; height: 1200px; overflow: hidden; }
  body {
    background: var(--backdrop);
    position: relative;
    font-family: "Tajawal", sans-serif;
    color: var(--ink-light);
  }
  .card {
    position: absolute;
    left: 171px;
    width: 826px;
    height: 472px;
    overflow: hidden;
    box-shadow: 0 3px 8px rgba(0,0,0,0.45);
  }
  .card--front { top: 106px; }
  .card--back { top: 638px; }
  .card__texture {
    position: absolute; inset: 0;
    background: linear-gradient(90deg, var(--card-red-deep), var(--card-red-light) 50%, var(--card-red));
  }
  .card__band {
    position: absolute; left: 0; right: 0; bottom: 0; height: 18px;
    background: var(--band-dark);
  }
  .brand {
    position: absolute; top: 186px; right: 62px;
    font-size: 34px; font-weight: 500; letter-spacing: 1px;
    direction: ltr;
  }
  .credentials {
    position: absolute; right: 62px; top: 313px;
    direction: rtl; text-align: right;
    font-size: 21px; line-height: 27px; font-weight: 400;
    letter-spacing: 0.5px;
    list-style: none;
  }
  .owner {
    position: absolute; right: 514px; top: 296px;
    direction: rtl; text-align: right;
  }
  .owner__name { font-family: "Aref Ruqaa", serif; font-size: 26px; line-height: 36px; }
  .owner__title { font-family: "Aref Ruqaa", serif; font-size: 17px; margin-right: 65px; line-height: 26px; }
  .contact {
    position: absolute; left: 60px; top: 398px;
    font-family: "Roboto", sans-serif; font-size: 22px;
    display: flex; align-items: center; gap: 6px; direction: ltr;
  }
  .contact svg { width: 18px; height: 18px; }
  .list {
    position: absolute; top: 164px;
    direction: rtl; text-align: right;
    list-style: none;
    font-size: 25px; line-height: 33px;
    letter-spacing: 0.5px;
  }
  .list--right { right: 85px; }
  .list--left { right: 443px; }
  .list li::after {
    content: "";
    display: inline-block; width: 8px; height: 8px; border-radius: 50%;
    background: var(--bullet); margin-right: 10px; vertical-align: middle;
  }
</style>
</head>
<body>
  <section class="card card--front">
    <div class="card__texture" role="img" aria-label="Vertical red stripe texture"></div>
    <div class="brand">MV Decor</div>
    <ul class="credentials">
      <li>ماجستير هندسة ديكور</li>
      <li>دبلوم عالي فن تشكيلي</li>
      <li>أكاديمية الفنون الحرة</li>
      <li>استشارات هندسية-فنية</li>
    </ul>
    <div class="owner">
      <p class="owner__name">المهندس / سامي يوسف الحداد</p>
      <p class="owner__title">أستاذ جامعي</p>
    </div>
    <div class="contact">
      <svg viewBox="0 0 24 24" aria-hidden="true"><path fill="#fff" d="M6.6 10.8a15.1 15.1 0 0 0 6.6 6.6l2.2-2.2a1 1 0 0 1 1-.25 11.4 11.4 0 0 0 3.6.57 1 1 0 0 1 1 1V20a1 1 0 0 1-1 1A17 17 0 0 1 3 4a1 1 0 0 1 1-1h3.5a1 1 0 0 1 1 1c0 1.25.2 2.45.57 3.57a1 1 0 0 1-.25 1z"/></svg>
      <span>39004512 / 66018820</span>
    </div>
    <div class="card__band"></div>
  </section>

  <section class="card card--back">
    <div class="card__texture" role="img" aria-label="Vertical red stripe texture"></div>
    <ul class="list list--right">
      <li>ماجستير هندسة ديكور</li>
      <li>دبلوم عالي فن تشكيلي</li>
      <li>أكاديمية الفنون الحرة</li>
      <li>استشارات هندسية-فنية</li>
    </ul>
    <ul class="list list--left">
      <li>ماجستير هندسة ديكور</li>
      <li>دبلوم عالي فن تشكيلي</li>
      <li>أكاديمية الفنون الحرة</li>
      <li>استشارات هندسية-فنية</li>
    </ul>
  </section>
</body>
</html>
```